Small environmental consultancy needs a simple but professional web design

We are a boutique environmental consultancyand contracting business located in Margaret River in the South West of Western Australia.

We have two arms
1) Consulting which offers environmental planning, management and assessment services primarily to local government and the development industry.
2) Contracting which implements on site plans and on ground works primarily involving revegetation, bush regeneration and environmental weed control.

We need a simple yet professional web design within the wordpress platform that commmunicates professionalism, experience and technical expertise without appearing too corporate.

Something like this structure appeals:
http://fernquill.net.au/environment-services/
or
http://www.tallowbrookenvironmental.com.au/index.php

(without the image gallery function)

Target Market(s)

Local Government Officers deciding on tenders;
Developers, Engineers, Town Planning consultants looking for environmental expertise

Industry/Entity Type

Business

Number of Pages Required

5+ page

Font styles to use
Sans Serif

Colors
33a6d7
9bcb3c

Requirements
Must have
• Pages required include:
• Home
• Environmental Planning and Management
• Revegetation and Regeneration Implementation (This page can mirror the Environmental Planning and Management page exactly in structure but with different text and images)
• About Us (I think that this page can be relatively simple and generic)
• Contact (I think that this page can be very simple and generic)
Nice to have
• An ability to start out basic and quicikly establish a website presence and then build in additional drop downs and pages over time.
Should not have
• It does not need a photo gallery page;
• It does not need a major amount of space dedicated to social media and blogs etc as this is not currently particularly active area for us

```html
<!DOCTYPE html>
<html lang="en">
<head>
<meta charset="utf-8">
<title>Tuart Ecoservices – Environmental Planning and Management</title>
<link rel="stylesheet" href="https://fonts.googleapis.com/css2?family=Open+Sans:wght@400;600;700&family=Teko:wght@400;500&display=swap">
<style>
:root{
  --blue:#33a6d7;
  --blue-dark:#1f86c4;
  --green:#9bcb3c;
  --green-dark:#6f9a1c;
  --text:#4a4a4a;
  --heading-dark:#3a3a3a;
  --footer-bg:#ebebeb;
  --line:#d6d6d6;
  --brown:#6b4a2a;
  --white:#ffffff;
  --icon:#a9a9a9;
}
*{box-sizing:border-box;margin:0;padding:0}
html,body{width:1064px;height:1200px;overflow:hidden}
body{position:relative;background:var(--white);font-family:"Open Sans",Arial,sans-serif;color:var(--text)}

.site-header{position:absolute;left:0;top:0;width:1064px;height:155px;
  background:linear-gradient(180deg,#ffffff 0%,#eef3f7 45%,#d9e3ec 75%,#c9d6e2 100%)}
.brand{position:absolute;left:66px;top:58px;display:flex;align-items:center;gap:10px}
.brand-mark{width:30px;height:30px;border-radius:50%;background:var(--green)}
.brand-name{font-size:25px;font-weight:600;color:var(--brown);letter-spacing:.2px}
.call-box{position:absolute;right:65px;top:32px;text-align:left}
.call-label{font-size:15px;font-weight:700;color:#111;line-height:18px}
.call-number{font-size:25px;font-weight:700;color:var(--blue);line-height:28px;letter-spacing:.5px}
.search{position:absolute;left:810px;top:93px;width:188px;height:25px;background:var(--white);
  border:1px solid #dfe4e8;border-radius:2px;font-size:12px;color:#555;padding:4px 8px}
.search svg{position:absolute;right:6px;top:5px}

.main-nav{position:absolute;left:0;top:155px;width:1064px;height:39px;background:var(--blue);
  border-bottom:2px solid #2a94c4}
.main-nav ul{list-style:none;display:flex;height:100%;padding-left:71px}
.main-nav li{font-size:12.3px;font-weight:600;color:var(--white);text-transform:uppercase;
  display:flex;align-items:center;padding:0 19px;height:100%}
.main-nav li.active{background:var(--blue-dark)}

.hero{position:absolute;left:0;top:194px;width:1064px;height:112px;
  background:linear-gradient(90deg,#4e4a36 0%,#8a7c55 18%,#a8a48a 40%,#c8d0c6 60%,#6f7560 80%,#3e4130 100%)}

.page{position:absolute;left:65px;top:340px;width:933px}
.page-title{font-family:"Teko",sans-serif;font-weight:500;font-size:37px;line-height:40px;color:var(--green);
  text-transform:uppercase;letter-spacing:.3px}
.page p{font-size:11.7px;line-height:18.8px}
.intro{position:absolute;left:0;top:56px;width:535px}
.intro p+p{margin-top:18px}
.feature-image{position:absolute;left:560px;top:59px;width:373px;height:253px;border:1px solid #333;
  background:radial-gradient(ellipse at 50% 45%,#cde88a 0%,#7fae3a 35%,#3e6420 65%,#1c2e10 100%)}
.full{position:absolute;left:0;top:355px;width:933px}
.full p+p{margin-top:18px}

.site-footer{position:absolute;left:0;top:910px;width:1064px;height:290px;background:var(--footer-bg);
  border-top:1px solid var(--line)}
.footer-heading{font-family:"Teko",sans-serif;font-size:20px;line-height:22px;color:var(--heading-dark);text-transform:uppercase}
.footer-col{position:absolute;top:28px}
.footer-col p{font-size:11.7px;line-height:18px;color:#333}
.col-about{left:65px}
.col-about .footer-heading,.col-site .footer-heading{margin-bottom:10px}
.col-site{left:333px}
.call-now{position:absolute;left:64px;top:139px}
.call-now .footer-heading{font-size:19px}
.call-now-number{display:flex;align-items:center;gap:6px;margin-top:4px;font-family:"Teko",sans-serif;
  font-size:32px;line-height:30px;color:var(--green)}
.col-contact{left:545px}
.field{position:absolute;height:33px;background:var(--white);border:1px solid #dcdcdc;font-size:13px;color:#aaa;padding:7px 12px}
.field svg{position:absolute;right:8px;top:7px}
.f-name{left:545px;top:67px;width:221px}
.f-email{left:776px;top:67px;width:221px}
.f-message{left:545px;top:108px;width:452px;height:64px}
.send-btn{position:absolute;left:545px;top:181px;width:138px;height:38px;
  background:linear-gradient(180deg,#9cc33a 0%,#7aa321 100%);border:1px solid #6b8f1c;
  color:var(--white);font-family:"Teko",sans-serif;font-size:20px;line-height:38px;text-align:center;text-transform:uppercase}
.footer-rule{position:absolute;left:65px;top:246px;width:956px;border-top:1px solid #d9d9d9}
.copyright{position:absolute;left:65px;top:261px;font-size:11.7px;color:#333}
</style>
</head>
<body>

<header class="site-header" role="img" aria-label="Misty blue mountain ranges background">
  <div class="brand">
    <span class="brand-mark"></span>
    <span class="brand-name">Tuart Ecoservices</span>
  </div>
  <div class="call-box">
    <div class="call-label">Call Us</div>
    <div class="call-number">0400 555 018</div>
  </div>
  <div class="search">Search
    <svg width="14" height="14" viewBox="0 0 14 14"><circle cx="6" cy="6" r="4.5" fill="none" stroke="#999" stroke-width="1.6"/><line x1="9.3" y1="9.3" x2="13" y2="13" stroke="#999" stroke-width="1.8"/></svg>
  </div>
</header>

<nav class="main-nav">
  <ul>
    <li>Home</li>
    <li class="active">Environmental Planning and Management</li>
    <li>Revegetation and Bush Regeneration</li>
    <li>About Us</li>
    <li>Contact</li>
  </ul>
</nav>

<div class="hero" role="img" aria-label="Sunlit forest with tall tree trunks and autumn leaves"></div>

<main class="page">
  <h1 class="page-title">Environmental Planning and Management</h1>
  <div class="intro">
    <p>Lorem ipsum dolor sit amet, consectetuer adipiscing elit, sed diam nonummy nibh euismod tincidunt ut laoreet dolore magna aliquam erat ullamcorper suscipit lobortis nisl ut aliquip ex ea commodo consequat. Lorem ipsum dolor sit amet, consectetuer adipiscing elit, sed diam nonummy nibh euismod tincidunt ut laoreet dolore magna aliquam erat volutpat. Ut wisi enim ad minim veniam, quis nostrud exerci tation ullamcorper suscipit lobortis nisl ut aliquip ex ea commodo consequat.Lorem ipsum dolor sit amet, consectetuer adipiscing elit, sed diam nonummy nibh euismod tincidunt ut laoreet dolore magna aliquam erat volutpat. Ut wisi enim ad minim veniam, quis nostrud exerci tation ullamcorper suscipit lobortis nisl ut aliquip ex ea commodo consequat.</p>
    <p>Lorem ipsum dolor sit amet, consectetuer adipiscing elit, sed diam nonummy nibh euismod tincidunt ut laoreet dolore magna aliquam erat volutpat. Ut wisi enim ad minim veniam, quis nostrud exerci tation ullamcorper suscipit lobortis nisl ut aliquip ex ea commodo consequat. Lorem ipsum dolor sit amet, consectetuer adipiscing elit, sed diam nonummy nibh euismod tincidunt ut laoreet dolore magna aliquam erat ullamcorper suscipit lobortis nisl ut aliquip ex ea commodo consequat.</p>
  </div>
  <div class="feature-image" role="img" aria-label="Glowing green globe encircled by a ring of paper-cut figures holding hands"></div>
  <div class="full">
    <p>Lorem ipsum dolor sit amet, consectetuer adipiscing elit, sed diam nonummy nibh euismod tincidunt ut laoreet dolore magna aliquam erat ullamcorper suscipit lobortis nisl ut aliquip ex ea commodo consequat. Lorem ipsum dolor sit amet, consectetuer adipiscing elit, sed diam nonummy nibh euismod tincidunt ut laoreet dolore magna aliquam erat volutpat. Ut wisi enim ad minim veniam, quis nostrud exerci tation ullamcorper suscipit lobortis nisl ut aliquip ex ea commodo consequat.Lorem ipsum dolor sit amet, consectetuer adipiscing elit, sed diam nonummy nibh euismod tincidunt ut laoreet dolore magna aliquam erat volutpat. Ut wisi enim ad minim veniam, quis nostrud exerci tation ullamcorper suscipit lobortis nisl ut aliquip ex ea commodo consequat.</p>
    <p>Lorem ipsum dolor sit amet, consectetuer adipiscing elit, sed diam nonummy nibh euismod tincidunt ut laoreet dolore magna aliquam erat volutpat. Ut wisi enim ad minim veniam, quis nostrud exerci tation ullamcorper suscipit lobortis nisl ut aliquip ex ea commodo consequat. Lorem ipsum dolor sit amet, consectetuer adipiscing elit, sed diam nonummy nibh euismod tincidunt ut laoreet dolore magna aliquam erat ullamcorper suscipit lobortis nisl ut aliquip ex ea commodo consequat.</p>
  </div>
</main>

<footer class="site-footer">
  <div class="footer-col col-about">
    <h2 class="footer-heading">About</h2>
    <p>Environmental Planning and Management<br>Revegetation and Bush Regeneration<br>Contacts</p>
  </div>
  <div class="call-now">
    <h2 class="footer-heading">Call us now:</h2>
    <div class="call-now-number">
      <svg width="20" height="20" viewBox="0 0 24 24"><path d="M6.6 10.8c1.4 2.8 3.8 5.1 6.6 6.6l2.2-2.2c.3-.3.7-.4 1-.2 1.1.4 2.3.6 3.6.6.6 0 1 .4 1 1V20c0 .6-.4 1-1 1C10.6 21 3 13.4 3 4c0-.6.4-1 1-1h3.5c.6 0 1 .4 1 1 0 1.3.2 2.5.6 3.6.1.3 0 .7-.2 1l-2.3 2.2z" fill="#555"/></svg>
      0400 555 018
    </div>
  </div>
  <div class="footer-col col-site">
    <h2 class="footer-heading">Website</h2>
    <p>www.tuartecoservices.com.au</p>
  </div>
  <div class="footer-col col-contact">
    <h2 class="footer-heading">Contact us</h2>
  </div>
  <div class="field f-name">Name
    <svg width="18" height="18" viewBox="0 0 18 18"><circle cx="9" cy="5" r="4" fill="#a9a9a9"/><path d="M1 18c0-5 3.5-7.5 8-7.5s8 2.5 8 7.5z" fill="#a9a9a9"/></svg>
  </div>
  <div class="field f-email">E-mail
    <svg width="20" height="16" viewBox="0 0 20 16"><rect x="0" y="1" width="20" height="14" rx="1" fill="#a9a9a9"/><path d="M0 2l10 7 10-7" fill="none" stroke="#fff" stroke-width="1.5"/></svg>
  </div>
  <div class="field f-message">Message
    <svg width="20" height="17" viewBox="0 0 20 17"><path d="M1 1h18v11H7l-4 4v-4H1z" fill="#a9a9a9"/><circle cx="6" cy="6.5" r="1.2" fill="#fff"/><circle cx="10" cy="6.5" r="1.2" fill="#fff"/><circle cx="14" cy="6.5" r="1.2" fill="#fff"/></svg>
  </div>
  <div class="send-btn">Send message</div>
  <div class="footer-rule"></div>
  <p class="copyright">© 2015 Tuart Ecoservices. All Rights Reserved.</p>
</footer>

</body>
</html>
```